KLW AUDITION

I need a post card design (front only) with this on it:
Bold Rising Steps (this is the main title to be in all caps)
Auditions
Date: Thursday June 30th
6:30-8:30 PM in person
Address: 4172 Fernwick BLVD, Oakland CA 94603
video submissions turn in by Sunday July 3rd, 2022 email:BoldRisingSteps22@tolvamail.com
Teens and Adults welcomed

SO PLEASE COME UP WITH A DESIGN THATS COLORFUL AND INVITING THX!

```html
<!DOCTYPE html>
<html lang="en">
<head>
<meta charset="utf-8">
<title>Bold Rising Steps Auditions – Postcard</title>
<link rel="stylesheet" href="https://fonts.googleapis.com/css2?family=Lexend:wght@600;700;800&family=Barlow+Semi+Condensed:wght@600;700&family=Audiowide&family=Montserrat:wght@500;700&display=swap">
<style>
  :root{
    --page:#e4e2df;
    --night-deep:#1a1a6e;
    --night-blue:#2433a8;
    --night-violet:#3a1678;
    --ray-blue:#5a6cff;
    --ray-violet:#b24be0;
    --mint:#14f0b4;
    --aqua:#4ee3f2;
    --pink:#f22ab4;
    --white:#ffffff;
    --ink:#0c1a3a;
  }
  *{margin:0;padding:0;box-sizing:border-box}
  html,body{width:769px;height:1200px;overflow:hidden;background:var(--page)}
  .canvas{position:relative;width:769px;height:1200px}
  .postcard{
    position:absolute;left:20px;top:357px;width:729px;height:486px;overflow:hidden;
    background:linear-gradient(100deg,var(--night-blue) 0%,var(--night-deep) 45%,var(--night-violet) 100%);
    box-shadow:0 6px 18px rgba(0,0,0,.35);
    text-align:center;color:var(--white);
  }
  .light-rays{
    position:absolute;inset:0;
    background:
      radial-gradient(ellipse 38% 55% at 8% 45%,rgba(90,108,255,.45),transparent 70%),
      radial-gradient(ellipse 38% 55% at 92% 45%,rgba(178,75,224,.45),transparent 70%),
      linear-gradient(180deg,transparent 60%,rgba(16,14,70,.6) 100%);
  }
  .line{position:absolute;left:0;width:100%;line-height:1}
  .title-top{
    top:44px;font-family:"Lexend",sans-serif;font-weight:700;font-size:50px;letter-spacing:0;
    background:linear-gradient(90deg,var(--mint),var(--aqua));
    -webkit-background-clip:text;background-clip:text;color:transparent;
  }
  .title-main{
    top:96px;font-family:"Lexend",sans-serif;font-weight:800;font-size:124px;letter-spacing:-2px;
    background:linear-gradient(180deg,var(--pink) 15%,var(--aqua) 80%);
    -webkit-background-clip:text;background-clip:text;color:transparent;
    -webkit-text-stroke:2px var(--mint);
  }
  .auditions{
    top:226px;font-family:"Lexend",sans-serif;font-weight:700;font-size:42px;
    background:linear-gradient(90deg,var(--aqua),var(--mint));
    -webkit-background-clip:text;background-clip:text;color:transparent;
  }
  .date-box{
    position:absolute;top:278px;left:235px;width:258px;height:35px;display:flex;
    border:2px solid var(--mint);font-family:"Barlow Semi Condensed",sans-serif;font-weight:700;font-size:26px;line-height:31px;
  }
  .date-box .day-date{background:var(--mint);color:var(--ink);width:46%}
  .date-box .day-date sup{font-size:13px;vertical-align:9px}
  .date-box .weekday{color:var(--mint);flex:1}
  .time{top:320px;font-family:"Barlow Semi Condensed",sans-serif;font-weight:700;font-size:21px}
  .time small{font-size:14px}
  .welcome{
    top:348px;font-family:"Audiowide",sans-serif;font-size:16px;letter-spacing:2.5px;
    color:transparent;-webkit-text-stroke:1px var(--mint);
  }
  .rule{position:absolute;left:50%;height:1px;transform:translateX(-50%)}
  .rule-teal{top:369px;width:220px;background:linear-gradient(90deg,transparent,var(--mint),transparent)}
  .rule-pink{top:417px;width:220px;background:linear-gradient(90deg,transparent,var(--pink),transparent)}
  .deadline-label{top:376px;font-family:"Montserrat",sans-serif;font-weight:500;font-size:10.5px;letter-spacing:4px}
  .deadline-date{top:393px;font-family:"Montserrat",sans-serif;font-weight:700;font-size:14px;color:var(--aqua)}
  .deadline-date sup{font-size:8px}
  .contact{
    position:absolute;top:425px;left:0;width:100%;display:flex;justify-content:center;gap:22px;
    font-family:"Montserrat",sans-serif;font-weight:700;font-size:10.5px;line-height:16px;
  }
  .contact-item{display:flex;align-items:center;gap:9px}
  .contact-item svg{flex:none}
</style>
</head>
<body>
<main class="canvas">
  <section class="postcard">
    <div class="light-rays" role="img" aria-label="Starry night sky with neon blue and violet light rays sweeping in from both sides"></div>

    <h1 class="line title-top">BOLD RISING</h1>
    <p class="line title-main">STEPS</p>
    <h2 class="line auditions">AUDITIONS</h2>

    <div class="date-box">
      <span class="day-date">30<sup>TH</sup> JUNE</span>
      <span class="weekday">THURSDAY</span>
    </div>

    <p class="line time">6:30PM – 8:30PM <small>(IN PERSON)</small></p>
    <p class="line welcome">TEENS AND ADULTS WELCOMED</p>
    <div class="rule rule-teal"></div>
    <p class="line deadline-label">VIDEO SUBMISSIONS TURN IN BY</p>
    <p class="line deadline-date">3<sup>rd</sup> JULY SUNDAY, 2022</p>
    <div class="rule rule-pink"></div>

    <div class="contact">
      <span class="contact-item">
        <svg width="14" height="16" viewBox="0 0 14 16" aria-hidden="true">
          <path d="M7 1a5 5 0 0 0-5 5c0 3.5 5 8 5 8s5-4.5 5-8a5 5 0 0 0-5-5z" fill="none" stroke="#f22ab4" stroke-width="2"/>
          <circle cx="7" cy="6" r="1.8" fill="#f22ab4"/>
        </svg>
        4172 FERNWICK BLVD, OAKLAND CA 94603
      </span>
      <span class="contact-item">
        <svg width="15" height="11" viewBox="0 0 15 11" aria-hidden="true">
          <rect x="1" y="1" width="13" height="9" fill="none" stroke="#f22ab4" stroke-width="1.6"/>
          <path d="M1 1l6.5 5L14 1M1 10l4.5-4M14 10L9.5 6" fill="none" stroke="#f22ab4" stroke-width="1.4"/>
        </svg>
        BoldRisingSteps22@tolvamail.com
      </span>
    </div>
  </section>
</main>
</body>
</html>
```